Quill Press Oceania needs a website

We require a website design which will be different to the normal websites that you visit. The objective of this website will be a call to action on the last page which will link to our email address so customers can email us their quotation requirements.

An example of how we envisage the look and the pages turning is as a flip books for example: https://www.vidharbor.example/watch?v=KtLmPzQa7Rw&feature=vh.be

page 1: just has our logo on it with the tag "Specialist producing quality printed books to your deadline."

Page 2: Black Page with white text "Black and White Book"
These are produced either digitally or offset on a complete range of stocks

Page 3: Colour books (use an image of your choice) These are also produced either digitally or offset plus we have the choice of web presses for larger print runs

Page 4: Digital books We do have a minimum run of 50 books using this process so a one off Thesis is not economically viable using this process. In special circumstance the digital process can produce books more quickly then by using our offset printing process.

Page 5: Having the complete range of printing machines at our disposal enables you to make a perfectly informed choice for your special project.

Then we need a special quote button which takes them directly to our email link. On this page we also need to add: We have had 25 years' experience printing books saving customers time and money whilst guaranteeing quality

Page 6: Logo repeated from page one with name: Morgan Elsworth and mobile phone no 0487 552 314

- Must follow the brief exactly. Must have a turn page book. Clear, simple and concise with a touch of creative flare and must lead into a call for action which is there quotation. A unique button for quotation link...something out of the ordinary which makes someone want to get a quote.

- It would be nice to have 3D Logo on Page 1 & 6.
a unique button for quotation link...something that make someone eager to proceed.

Our main objective is that they should not leave our website without giving us a quote. Please make sure that the spelling is correct and we do not require clip art images. Continue the logo colours through the theme
Updates

here is another example www.vidharbor.example/watch?v=JbXo412TrGe Added Saturday, May 13, 2017

Target Market(s)

Schools, Universities, Self Publishers, Publishers, Graphic Designers, Conference Providers, Businesses, Corporations, Government.

Industry/Entity Type

Printing

Coding

Coded - Design and coding required

Number of Pages Required

5+ page

Font styles to use
Sans Serif

Colors
34a6d7
ec1f27
fbed22
9bcb3c
ffc214
6b449b

Requirements
Must have
• Must follow the brief exactly. Must have a turn page book. Clear, simple and concise with a touch of creative flare and must lead into a call for action which is there quotation. A unique button for quotation link...something out of the ordinary which makes someone want to get a quote. would like to see the colours of the logo use throughout
Nice to have
• 3D Logo on Page 1 & 6.
• a unique button for quotation link...something that make someone eager to proceed.
• Our main objective is that they should not leave our website without giving us a quote
Should not have
• Spelling mistakes, clip art, ordinary design

```html
<!DOCTYPE html>
<html lang="en">
<head>
<meta charset="utf-8">
<title>Quill Press Oceania — Contact</title>
<link rel="stylesheet" href="https://fonts.googleapis.com/css2?family=Jost:wght@400;500;600&display=swap">
<style>
  :root {
    --purple: #6b449b;
    --purple-soft: #7b56ad;
    --cyan: #34a6d7;
    --red: #ec1f27;
    --amber: #ffc214;
    --ink: #222222;
    --paper: #fbfaf6;
  }
  * { margin: 0; padding: 0; box-sizing: border-box; }
  html, body { width: 720px; height: 1200px; overflow: hidden; background: var(--paper); }
  body { font-family: "Jost", sans-serif; color: var(--ink); }
  .page {
    position: relative;
    width: 720px;
    height: 1200px;
    overflow: hidden;
  }
  .backdrop {
    position: absolute;
    inset: 0;
    background:
      linear-gradient(160deg, rgba(255,236,150,0.45) 0%, rgba(255,255,255,0) 30%),
      linear-gradient(200deg, rgba(140,215,240,0.35) 10%, rgba(255,255,255,0) 45%),
      linear-gradient(20deg, rgba(255,180,215,0.45) 0%, rgba(255,240,160,0.5) 35%, rgba(255,255,255,0) 60%),
      radial-gradient(ellipse at 50% 45%, #ffffff 0%, #fbfaf7 55%, #f2f0ec 100%);
  }
  .content {
    position: relative;
    text-align: center;
  }
  .brand {
    position: absolute;
    top: 372px;
    left: 0;
    width: 720px;
    font-size: 40px;
    font-weight: 500;
    color: var(--ink);
    letter-spacing: 0.5px;
  }
  .tagline {
    position: absolute;
    top: 494px;
    left: 90px;
    width: 540px;
    font-size: 24.5px;
    line-height: 36px;
    font-weight: 500;
    color: var(--purple-soft);
  }
  .contact-label {
    position: absolute;
    top: 632px;
    left: 0;
    width: 720px;
    font-size: 25px;
    font-weight: 500;
    color: var(--cyan);
  }
  .contact-name {
    position: absolute;
    top: 662px;
    left: 0;
    width: 720px;
    font-size: 40px;
    font-weight: 600;
    color: var(--red);
  }
  .contact-row {
    position: absolute;
    left: 0;
    width: 720px;
    display: flex;
    justify-content: center;
    align-items: center;
    gap: 10px;
  }
  .contact-row .icon {
    width: 36px;
    height: 36px;
    border-radius: 50%;
    display: flex;
    align-items: center;
    justify-content: center;
    flex: none;
  }
  .phone-row { top: 744px; }
  .phone-row .icon { background: var(--amber); }
  .phone-number { font-size: 31px; font-weight: 600; letter-spacing: 1px; color: var(--ink); }
  .email-row { top: 792px; gap: 12px; }
  .email-row .icon { background: var(--purple); }
  .email-address { font-size: 18.5px; font-weight: 500; color: var(--ink); }
</style>
</head>
<body>
  <main class="page">
    <div class="backdrop" role="img" aria-label="Soft background photo of colour print proof sheets with calibration bars"></div>
    <section class="content">
      <h1 class="brand">Quill Press Oceania</h1>
      <p class="tagline">We have had 25 years' experience printing books, saving customers time and money whilst guaranteeing quality</p>
      <p class="contact-label">Contact</p>
      <h2 class="contact-name">Morgan Elsworth</h2>
      <div class="contact-row phone-row">
        <span class="icon">
          <svg width="20" height="20" viewBox="0 0 24 24" aria-hidden="true">
            <path fill="#ffffff" d="M6.6 10.8a15.1 15.1 0 0 0 6.6 6.6l2.2-2.2a1 1 0 0 1 1-.25 11.4 11.4 0 0 0 3.6.57 1 1 0 0 1 1 1V20a1 1 0 0 1-1 1A17 17 0 0 1 3 4a1 1 0 0 1 1-1h3.5a1 1 0 0 1 1 1c0 1.25.2 2.45.57 3.6a1 1 0 0 1-.25 1z"/>
          </svg>
        </span>
        <span class="phone-number">0487 552 314</span>
      </div>
      <div class="contact-row email-row">
        <span class="icon">
          <svg width="18" height="18" viewBox="0 0 24 24" aria-hidden="true">
            <rect x="2.5" y="5" width="19" height="14" rx="2" fill="#ffffff"/>
            <path d="M3.5 6.5 12 13l8.5-6.5" fill="none" stroke="#6b449b" stroke-width="2"/>
          </svg>
        </span>
        <span class="email-address">me@quillpressoceania.example</span>
      </div>
    </section>
  </main>
</body>
</html>
```